business card for a massage therapy practice named 'Cedar and Willow Massage Studio'

I really need a trendy, yet easy on the eyes business card to complement my logo. Ideally with some gold or rose gold foil work.

My uploaded file of the logo I have in horizontal but I have a vertical version as well. Another color that is used in the website is a blush pink here and there. I'd like to see some trendy tropical leaves in the design.

```html
<!DOCTYPE html>
<html lang="en">
<head>
<meta charset="utf-8">
<title>Cedar and Willow Massage Studio – Business Card</title>
<link href="https://fonts.googleapis.com/css2?family=Questrial&display=swap" rel="stylesheet">
<style>
  :root {
    --stage: #2a2a2a;
    --mint: #84ceb8;
    --card-white: #f7f9fa;
    --ink: #1d1d1d;
    --gold: #9a7f55;
    --grey: #5a5a5a;
    --leaf-soft: #dbe8cf;
    --leaf-mid: #a9c98c;
  }
  * { margin: 0; padding: 0; box-sizing: border-box; }
  html, body { width: 1200px; height: 800px; overflow: hidden; }
  body {
    background: var(--stage);
    font-family: "Questrial", sans-serif;
    position: relative;
  }
  .card {
    position: absolute;
    width: 580px;
    height: 330px;
    border-radius: 2px;
    overflow: hidden;
  }
  .card-front { left: 500px; top: 70px; background: var(--mint); }
  .card-back { left: 150px; top: 390px; background: var(--card-white); }

  .brand { display: flex; align-items: center; gap: 14px; position: absolute; }
  .brand-dot { border-radius: 50%; background: var(--gold); flex: none; }
  .brand-name { color: var(--ink); line-height: 1.15; }
  .brand-name span { display: block; }

  .card-front .brand { left: 110px; top: 100px; }
  .card-front .brand-dot { width: 46px; height: 46px; }
  .card-front .brand-name { font-size: 38px; }
  .card-front .brand-name .sub { font-size: 19px; letter-spacing: 4px; text-transform: uppercase; }

  .front-web {
    position: absolute; left: 0; right: 0; bottom: 48px;
    text-align: center; color: #fff; font-size: 15px; letter-spacing: 1.5px;
  }

  .card-back .brand { left: 36px; top: 34px; }
  .card-back .brand-dot { width: 32px; height: 32px; }
  .card-back .brand-name { font-size: 26px; }
  .card-back .brand-name .sub { font-size: 13px; letter-spacing: 3px; text-transform: uppercase; }

  .person { position: absolute; left: 40px; top: 160px; }
  .person-name { color: var(--gold); font-size: 30px; letter-spacing: 1px; }
  .person-role { color: var(--grey); font-size: 18px; margin-top: -2px; }

  .contact { position: absolute; left: 40px; top: 236px; list-style: none; font-size: 18px; color: var(--grey); line-height: 1.45; }
  .contact .label { color: var(--gold); }

  .leaf-art {
    position: absolute; left: 390px; top: 70px;
    width: 190px; height: 180px;
    background: linear-gradient(160deg, var(--leaf-mid) 0%, var(--leaf-soft) 55%, var(--card-white) 100%);
  }
</style>
</head>
<body>
  <section class="card card-front">
    <div class="brand">
      <div class="brand-dot"></div>
      <div class="brand-name"><span>Cedar and Willow</span><span class="sub">Massage Studio</span></div>
    </div>
    <p class="front-web">www.yourwebsite.com</p>
  </section>

  <section class="card card-back">
    <div class="brand">
      <div class="brand-dot"></div>
      <div class="brand-name"><span>Cedar and Willow</span><span class="sub">Massage Studio</span></div>
    </div>
    <div class="leaf-art" role="img" aria-label="Illustration area: green tropical palm frond"></div>
    <div class="person">
      <p class="person-name">Lena Hart</p>
      <p class="person-role">Artist</p>
    </div>
    <ul class="contact">
      <li><span class="label">Phone:</span> +123 456 789 0</li>
      <li><span class="label">Email:</span> lorem@ipsum.com</li>
      <li><span class="label">Web:</span> www.yourwebsite.com</li>
    </ul>
  </section>
</body>
</html>
```